I need the Scorecard I've developed for my staff to be produced into a visually engaging piece that will encourage the staff to utilize it on a daily basis. I'm thinking it could be 5x7 in size so that it isn't too cumbersome, but I'm open to different layouts.
I have multiple other departments that will need Scorecards created for them as well, but each one will contain task specific questions for each department.

```html
<!DOCTYPE html>
<html lang="en">
<head>
<meta charset="utf-8">
<title>Receptionist Daily Excellence Scorecard</title>
<link href="https://fonts.googleapis.com/css2?family=Arimo:wght@400;600;700&family=Roboto+Condensed:wght@400;700&display=swap" rel="stylesheet">
<style>
:root{
  --frame:#d8262c;
  --title:#0d4c92;
  --dark:#5f5a59;
  --ink:#222;
  --blue-head:#8fcdf0; --blue-row:#cfe6f6;
  --yellow-head:#e5ca7a; --yellow-row:#fbe9a3;
  --purple-head:#c0b6d9; --purple-row:#e4e0ef;
  --pink-head:#e096b0; --pink-row:#f8d5e3;
  --green-head:#aacf62; --green-row:#d4e8a2;
  --peach-head:#e9c09e; --peach-row:#f2dcc6;
  --grey-row:#dedede;
  --mint-head:#7fbf9a; --mint-row:#cce5d6;
  --orange-head:#f0a150; --orange-row:#f6d5b2;
  --mauve-row:#e2cadc;
  --red:#d8262c; --cyan:#1a8fd0; --green:#1b9a3c;
}
*{box-sizing:border-box;margin:0;padding:0}
html,body{width:1200px;height:2629px;overflow:hidden;background:#fff}
body{position:relative;font-family:"Arimo",Arial,sans-serif;color:var(--ink)}
.frame{position:absolute;left:28px;top:42px;width:1144px;height:2543px;border:3px solid var(--frame)}
.portrait{position:absolute;left:52px;top:62px;width:114px;height:141px;border:3px solid #b9b3cc;border-radius:8px;background:linear-gradient(180deg,#e9e4e0,#c9b9ad 60%,#f4f2f0)}
.title{position:absolute;left:190px;top:56px;width:950px;height:56px}
.title svg{display:block;width:950px;height:56px}
.title text{font-family:"Roboto Condensed",sans-serif;font-size:56px;fill:var(--title)}
.field{position:absolute;border:2px solid #555;font-size:20px;padding:0 8px;display:flex;align-items:center}
.field--name{left:190px;top:122px;width:545px;height:38px}
.field--loc{left:190px;top:167px;width:545px;height:38px}
.field--loc .date{position:absolute;left:318px}
.rating-key{position:absolute;left:745px;top:122px;width:405px;height:84px;border:2px solid #555;text-align:center;font-family:"Roboto Condensed",sans-serif}
.rating-key p{font-size:21px;margin-top:12px;white-space:nowrap}
.rating-key svg{display:block;margin:10px auto 0;width:389px;height:22px}
.rating-key svg text{font-family:"Roboto Condensed",sans-serif;font-size:17px}
.section{position:absolute;left:52px;width:1096px}
.bar{height:40px;border-radius:20px 20px 0 0;background:var(--dark);color:#fff;font-weight:700;font-size:29px;display:flex;align-items:center;justify-content:center;gap:14px;position:relative;letter-spacing:.3px;white-space:nowrap}
.bar svg{width:40px;height:40px;margin-top:-14px}
.bar svg.side{position:absolute;left:200px;top:-8px;margin:0}
.grid{display:grid;grid-template-columns:536px 252px 304px;gap:2px;margin-top:4px}
.grid div{height:42px;background:var(--row);font-size:22px;display:flex;align-items:center;padding-left:20px;white-space:nowrap}
.grid .h{background:var(--head);font-size:26px}
.grid .h.c{justify-content:center;padding-left:0}
.blue{--head:var(--blue-head);--row:var(--blue-row)}
.yellow{--head:var(--yellow-head);--row:var(--yellow-row)}
.purple{--head:var(--purple-head);--row:var(--purple-row)}
.pink{--head:var(--pink-head);--row:var(--pink-row)}
.green{--head:var(--green-head);--row:var(--green-row)}
.peach{--head:var(--peach-head);--row:var(--peach-row)}
.lines{margin-top:4px;display:flex;flex-direction:column;gap:4px}
.line{height:40px;display:flex;align-items:center;font-size:22px;padding-left:52px;background:var(--row);white-space:nowrap}
.line .fill{flex:1;border-bottom:1px dotted #777;height:22px;margin:0 50px 0 6px}
.status .line{background:var(--grey-row);padding-left:0}
.status .dot{width:34px;height:34px;border-radius:50%;background:#fff;margin:0 40px 0 75px;flex:0 0 34px}
.status .lvl{width:226px}
.reflect{--row:var(--mint-row)}
.reflect .bar{background:var(--mint-head)}
.flags{--row:var(--orange-row)}
.flags .bar{background:var(--orange-head)}
.flags .line{padding-left:26px}
.flags .line svg{width:22px;height:22px;margin-right:10px}
.manager{width:640px;--row:var(--mauve-row)}
.manager .line{padding-left:48px}
.manager .line .fill{flex:0 0 146px}
.signs{position:absolute;left:710px;top:2424px;width:438px;height:130px;border:2px solid var(--title);border-radius:12px;font-family:"Roboto Condensed",sans-serif;font-size:25px;line-height:1;padding:12px 16px 0 16px}
.signs p{display:flex;align-items:flex-end;height:37px;white-space:nowrap}
.signs .fill{flex:1;border-bottom:1px dotted #777;margin-left:6px;height:18px}
.signs .date{padding-left:126px}
</style>
</head>
<body>
<div class="frame"></div>
<div class="portrait" role="img" aria-label="Staff member portrait photo"></div>
<h1 class="title"><svg viewBox="0 0 950 56"><text x="0" y="49" textLength="950" lengthAdjust="spacingAndGlyphs"><tspan font-weight="700">RECEPTIONIST</tspan> <tspan font-weight="400">DAILY EXCELLENCE SCORECARD</tspan></text></svg></h1>
<div class="field field--name">Name :</div>
<div class="field field--loc">Location :<span class="date">Date :</span></div>
<div class="rating-key"><p>Please Rate yourself for each task</p>
<svg viewBox="0 0 389 22"><text x="0" y="17" textLength="389" lengthAdjust="spacingAndGlyphs"><tspan fill="#d8262c">1 = Needs Improvement</tspan>  <tspan fill="#1a8fd0">3 = Meets Expectations</tspan>  <tspan fill="#1b9a3c">5 = Excellent</tspan></text></svg></div>

<section class="section blue" style="top:222px">
<div class="bar"><svg viewBox="0 0 40 40"><rect x="8" y="8" width="22" height="28" rx="2" fill="#1a6fc0"/><path d="M12 16h14M12 22h14M12 28h10" stroke="#fff" stroke-width="2"/><path d="M11 5v6M16 5v6M21 5v6M26 5v6" stroke="#1a6fc0" stroke-width="2"/></svg>1. Call Handling &amp; First Call Intake</div>
<div class="grid"><div class="h">Task</div><div class="h c">Self-Rating (1-5)</div><div class="h c">Notes / Issues</div>
<div>Answered 90%+ calls within 3 rings</div><div></div><div></div>
<div>Maintained empathy and professionalism</div><div></div><div></div>
<div>Accurately completed all First Call fields</div><div></div><div></div>
<div>Worked within Receptionist role</div><div></div><div></div></div>
</section>

<section class="section yellow" style="top:500px">
<div class="bar"><svg class="side" viewBox="0 0 40 40" style="left:196px"><path d="M12 4c-4 2-5 6-4 11 2 8 7 15 14 19 4 2 7 1 9-2l-5-6-4 2c-3-2-6-7-7-11l4-2-3-9z" fill="#ef7d22"/></svg>2. Call Management During Busy Times</div>
<div class="grid"><div class="h">Task</div><div class="h c">Self-Rating (1-5)</div><div class="h c">Notes / Issues</div>
<div>Prioritized urgent vs. non-urgent calls</div><div></div><div></div>
<div>Hold times under 1 minute</div><div></div><div></div>
<div>Logged all calls</div><div></div><div></div>
<div>Requested help if overwhelmed</div><div></div><div></div></div>
</section>

<section class="section purple" style="top:779px">
<div class="bar"><svg viewBox="0 0 40 40" style="width:50px"><rect x="3" y="8" width="34" height="26" rx="2" fill="#8e82c0"/><g fill="#fff"><rect x="7" y="15" width="5" height="4"/><rect x="14" y="15" width="5" height="4"/><rect x="21" y="15" width="5" height="4"/><rect x="28" y="15" width="5" height="4"/><rect x="7" y="22" width="5" height="4"/><rect x="14" y="22" width="5" height="4"/><rect x="21" y="22" width="5" height="4"/><rect x="28" y="22" width="5" height="4"/></g></svg>3. Scheduling Accuracy</div>
<div class="grid"><div class="h">Task</div><div class="h c">Self-Rating (1-5)</div><div class="h c">Notes / Issues</div>
<div>Updated scheduling board</div><div></div><div></div>
<div>Cross-checked with Red Book</div><div></div><div></div>
<div>Entered manifold info promptly</div><div></div><div></div></div>
</section>

<section class="section pink" style="top:1011px">
<div class="bar"><svg viewBox="0 0 40 40"><path d="M13 4l-10 6 4 8 4-2v22h18V16l4 2 4-8-10-6c-1 3-4 5-7 5s-6-2-7-5z" fill="#c2436f"/></svg>4. Clothing &amp; Flowers</div>
<div class="grid"><div class="h">Task</div><div class="h c">Self-Rating (1-5)</div><div class="h c">Notes / Issues</div>
<div>Clothing sheet completed</div><div></div><div></div>
<div>Family contact noted on sheet</div><div></div><div></div>
<div>Floral deliveries logged</div><div></div><div></div>
<div>Concerns communicated to</div><div></div><div></div>
<div>Care Center</div><div></div><div></div>
<div>Flower placement verified</div><div></div><div></div></div>
</section>

<section class="section green" style="top:1380px">
<div class="bar"><svg viewBox="0 0 40 40"><rect x="8" y="4" width="26" height="32" rx="2" fill="none" stroke="#8cc63f" stroke-width="2"/><path d="M13 12h16M13 18h16M13 24h10" stroke="#8cc63f" stroke-width="2"/><circle cx="11" cy="28" r="5" fill="none" stroke="#8cc63f" stroke-width="2"/></svg>5. Death Certificates</div>
<div class="grid"><div class="h">Task</div><div class="h c">Self-Rating (1-5)</div><div class="h c">Notes / Issues</div>
<div>Verified recipient ID&amp; relationship</div><div></div><div></div>
<div>Confirmed correct documents enclosed</div><div></div><div></div>
<div>Recipient signed the DC logbook</div><div></div><div></div>
<div>Suggested proofreading before leaving</div><div></div><div></div></div>
</section>

<section class="section peach" style="top:1660px">
<div class="bar"><svg viewBox="0 0 40 40" style="width:46px;height:46px"><path d="M20 4c10 0 17 6 17 13s-7 13-17 13c-2 0-4 0-5-1l-9 6 3-8c-4-3-6-6-6-10C3 10 10 4 20 4z" fill="#e9a87a"/><g fill="#fff"><circle cx="13" cy="17" r="2.2"/><circle cx="20" cy="17" r="2.2"/><circle cx="27" cy="17" r="2.2"/></g></svg>6. Routing &amp; Messages</div>
<div class="grid"><div class="h">Task</div><div class="h c">Self-Rating (1-5)</div><div class="h c">Notes / Issues</div>
<div>Calls routed appropriately</div><div></div><div></div>
<div>Messages included all required info</div><div></div><div></div>
<div>Delivered 95%+ messages in 30 min</div><div></div><div></div></div>
</section>

<section class="section status" style="top:1905px">
<div class="bar"><svg viewBox="0 0 40 40"><rect x="7" y="2" width="28" height="36" fill="#3a3534" transform="rotate(-8 20 20)"/><path d="M13 10h16M13 16h16M13 22h12" stroke="#fff" stroke-width="2"/><path d="M14 34v-5M19 34v-8M24 34v-4M29 34v-7" stroke="#fff" stroke-width="3"/></svg>Daily Status Summary (Tick One)</div>
<div class="lines">
<div class="line"><span class="dot"></span><span class="lvl">Excellent</span>All key duties completed, proactive, calm under pressure</div>
<div class="line"><span class="dot"></span><span class="lvl">Satisfactory</span>Most duties completed, minor follow-up needed</div>
<div class="line"><span class="dot"></span><span class="lvl">Needs Support</span>Missed urgent duties, accuracy or stress issues</div>
</div>
</section>

<section class="section reflect" style="top:2098px">
<div class="bar"><svg viewBox="0 0 40 40"><rect x="6" y="6" width="24" height="30" rx="2" fill="none" stroke="#4e8f6a" stroke-width="2"/><path d="M10 14h14M10 20h14M10 26h10" stroke="#4e8f6a" stroke-width="2"/><path d="M34 8l-12 18-2 6 5-3 12-18z" fill="#4e8f6a"/></svg>Daily Reflection</div>
<div class="lines">
<div class="line">What went well today ?<span class="fill"></span></div>
<div class="line">Any issues or barriers to note ?<span class="fill"></span></div>
<div class="line">Support needed from supervisor ?<span class="fill"></span></div>
</div>
</section>

<section class="section flags" style="top:2280px">
<div class="bar">&#9733; Stars &amp; <svg viewBox="0 0 40 40" style="width:32px;height:32px;margin:0"><path d="M8 4v34" stroke="#fff" stroke-width="3"/><path d="M9 6c8-4 12 4 24 0v16c-12 4-16-4-24 0z" fill="#fff"/></svg> Flags (Supervisor Use Only)</div>
<div class="lines">
<div class="line"><svg viewBox="0 0 24 24"><path d="M12 2l3 7 7 .6-5.3 4.6 1.6 7.3L12 17.8 5.7 21.5l1.6-7.3L2 9.6 9 9z" fill="#7a3b2a"/></svg>Excellence or above-and-beyond moments<span class="fill"></span></div>
<div class="line"><svg viewBox="0 0 24 24"><path d="M5 2v20" stroke="#7a3b2a" stroke-width="2"/><path d="M6 3c5-2 8 3 15 0v10c-7 3-10-2-15 0z" fill="#7a3b2a"/></svg>Concerns needing follow-up/coaching<span class="fill"></span></div>
</div>
</section>

<section class="section manager" style="top:2424px">
<div class="bar"><svg viewBox="0 0 40 40"><path d="M6 18h7v18H6zM15 18l6-12c3 0 4 2 3 6l-1 4h10c2 0 3 2 2 4l-3 13c-1 2-2 3-4 3H15z" fill="#fff"/></svg>Manager's Overall Rating</div>
<div class="lines">
<div class="line">Please rate overall performance on a 1-5 scale</div>
<div class="line">Manager Overall Rating<span class="fill"></span></div>
</div>
</section>

<div class="signs">
<p>Receptionist Sign.<span class="fill"></span></p>
<p>Supervisor Sign.<span class="fill"></span></p>
<p class="date">Date<span class="fill"></span></p>
</div>
</body>
</html>
```